New Business Card Design Project

I need a design for business cards, i am an electrical business called "Corvane Electrical and Communications" i need the cards to be double sided with the company logo on the back (attached) the front needs to say my company name, web site, email address, telephone number, and ABN number and electrical license number. I am open to different arrangements of the information but would like the background to be incorporating something electrical or something that looks smart. open to all additional ideas also.

The company colours are orange and grey see logo attached.

Business Name: Corvane Electrical and Communications
Website: corvaneelectricalandcomms.example.com.au
Email: brent@corvaneelectricalandcomms.example.com.au
Telephone(mobile): 0481209736
ABN: 71208349162
Lic No: 418273D

Target Market(s)

Business entities, Project Managers, Accounts, Clients

Industry/Entity Type

Electrician

Contact Information for Business Card

I need a design for business cards, i am an electrical business called "Corvane Electrical and Communications" i need the cards to be double sided with the company logo on the back (attached) the front needs to say my company name

Font styles to use
Serif
Sans Serif

Colors
f37122
5c5c5c

Requirements
Must have
• Must have the Logo on the back open to different ways of it being on the back but had in mind to keep it central but again open to other options
Nice to have
• A real modern cool background that is eye catching yet contemporary
Should not have
• No backgrounds of a light bulb or plug or anything like that

```html
<!DOCTYPE html>
<html lang="en">
<head>
<meta charset="utf-8">
<title>Corvane Electrical and Communications – Business Card</title>
<link rel="stylesheet" href="https://fonts.googleapis.com/css2?family=Saira:wght@400;500;600&display=swap">
<style>
  :root {
    --page-bg: #8e8f91;
    --card-dark: #49494b;
    --card-light: #e9e9ea;
    --band-light: #e4e4e6;
    --orange: #f0a323;
    --grey-text: #4d4d4f;
    --white-text: #f2f2f2;
    --rule: #8a8a8c;
  }
  * { box-sizing: border-box; margin: 0; padding: 0; }
  html, body {
    width: 1105px; height: 1200px; overflow: hidden;
    background: var(--page-bg);
    font-family: "Saira", "Arial", sans-serif;
  }
  .sheet { position: relative; width: 1105px; height: 1200px; }
  .card {
    position: absolute; left: 102px; width: 900px; height: 516px; overflow: hidden;
  }
  .card--front { top: 56px; background: var(--card-dark); }
  .card--back { top: 628px; background: var(--card-light); }

  /* wordmark */
  .wordmark { position: absolute; display: flex; align-items: center; gap: 18px; color: var(--orange); font-weight: 500; }
  .wordmark__dot { flex: none; border-radius: 50%; background: var(--orange); }
  .wordmark__name { display: block; letter-spacing: 0.06em; line-height: 1; }
  .wordmark__sub { display: block; letter-spacing: 0.05em; line-height: 1; }

  .card--front .wordmark { left: 44px; top: 70px; }
  .card--front .wordmark__dot { width: 26px; height: 26px; }
  .card--front .wordmark__name { font-size: 62px; margin-bottom: 8px; }
  .card--front .wordmark__sub { font-size: 18px; }

  .card--back .wordmark { left: 50%; top: 50%; transform: translate(-50%, -50%); color: var(--grey-text); }
  .card--back .wordmark__dot { width: 34px; height: 34px; }
  .card--back .wordmark__name { font-size: 92px; margin-bottom: 10px; }
  .card--back .wordmark__sub { font-size: 26px; }

  /* holder */
  .holder { position: absolute; right: 40px; top: 240px; text-align: right; }
  .holder__name { color: var(--orange); font-size: 32px; font-weight: 400; letter-spacing: 0.03em; line-height: 1.1; }
  .holder__role { color: var(--white-text); font-size: 22px; letter-spacing: 0.03em; line-height: 1.3; }
  .holder-rule { position: absolute; left: 42px; right: 40px; top: 306px; height: 1px; background: var(--rule); }

  /* contacts */
  .contacts { position: absolute; left: 42px; top: 340px; list-style: none; }
  .contacts__item { display: flex; align-items: center; gap: 14px; color: var(--white-text); height: 34px; font-size: 19px; }
  .contacts__item--phone { font-size: 24px; }
  .contacts__icon { width: 20px; height: 20px; flex: none; }

  .credentials { position: absolute; right: 40px; top: 368px; text-align: right; color: var(--white-text); font-size: 23px; line-height: 34px; letter-spacing: 0.02em; }

  .foot-band { position: absolute; left: 0; right: 0; bottom: 0; height: 43px; background: var(--band-light); border-top: 4px solid var(--orange); }
</style>
</head>
<body>
<main class="sheet">

  <section class="card card--front" aria-label="Business card front">
    <div class="wordmark">
      <span class="wordmark__dot"></span>
      <span>
        <span class="wordmark__name">CORVANE</span>
        <span class="wordmark__sub">ELECTRICAL &amp; COMMUNICATIONS</span>
      </span>
    </div>

    <div class="holder">
      <p class="holder__name">BRENT HALLOWAY</p>
      <p class="holder__role">CEO/FOUNDER</p>
    </div>
    <div class="holder-rule"></div>

    <ul class="contacts">
      <li class="contacts__item contacts__item--phone">
        <svg class="contacts__icon" viewBox="0 0 20 20" aria-hidden="true"><rect x="4" y="1" width="12" height="18" rx="2" fill="none" stroke="#f0a323" stroke-width="2"/><rect x="8" y="15" width="4" height="1.8" fill="#f0a323"/></svg>
        0481209736
      </li>
      <li class="contacts__item">
        <svg class="contacts__icon" viewBox="0 0 20 20" aria-hidden="true"><rect x="1" y="4" width="18" height="12" fill="#f0a323"/><path d="M1 4 L10 11 L19 4" fill="none" stroke="#49494b" stroke-width="1.6"/></svg>
        brent@corvaneelectricalandcomms.example.com.au
      </li>
      <li class="contacts__item">
        <svg class="contacts__icon" viewBox="0 0 20 20" aria-hidden="true"><circle cx="10" cy="10" r="9" fill="#f0a323"/><path d="M4 7 Q8 5 9 9 Q10 13 13 12 M12 4 Q14 7 17 8" fill="none" stroke="#49494b" stroke-width="1.6"/></svg>
        corvaneelectricalandcomms.example.com.au
      </li>
    </ul>

    <div class="credentials">
      <p>ABN: 71208349162</p>
      <p>Lic No: 418273D</p>
    </div>

    <div class="foot-band"></div>
  </section>

  <section class="card card--back" aria-label="Business card back">
    <div class="wordmark">
      <span class="wordmark__dot"></span>
      <span>
        <span class="wordmark__name">CORVANE</span>
        <span class="wordmark__sub">ELECTRICAL &amp; COMMUNICATIONS</span>
      </span>
    </div>
  </section>

</main>
</body>
</html>
```